Business card design for my company.
I would like the card's background colour to be black. You can also see our web site to get an idea of our brand. https://www.tmwhomecrafting.com.au/
- Name
- Email

```html
<!DOCTYPE html>
<html lang="en">
<head>
<meta charset="utf-8">
<title>TMW Home Crafting – Business Card</title>
<link rel="stylesheet" href="https://fonts.googleapis.com/css2?family=Montserrat:wght@400;500;700&family=Questrial&display=swap">
<style>
  :root {
    --page-bg: #d9d9d9;
    --card-bg: #363738;
    --white: #ffffff;
    --light: #e6e6e6;
    --green: #1e9a4a;
    --muted: #cfcfcf;
  }
  * { margin: 0; padding: 0; box-sizing: border-box; }
  html, body {
    width: 1200px;
    height: 1043px;
    overflow: hidden;
    background: var(--page-bg);
  }
  .canvas {
    position: relative;
    width: 1200px;
    height: 1043px;
  }
  .card {
    position: absolute;
    left: 202px;
    width: 804px;
    height: 430px;
    background: var(--card-bg);
    box-shadow: 0 6px 18px rgba(0,0,0,0.25);
  }
  .card--front { top: 108px; }
  .card--back  { top: 584px; }

  .brand {
    position: absolute;
    left: 0;
    right: 0;
    text-align: center;
    color: var(--white);
    font-family: "Montserrat", sans-serif;
    font-weight: 700;
    line-height: 1;
  }
  .card--front .brand { top: 120px; }
  .card--back .brand  { top: 150px; }
  .brand__mark {
    display: inline-block;
    width: 16px;
    height: 16px;
    background: var(--green);
    margin-right: 14px;
    vertical-align: middle;
  }
  .brand__name {
    display: inline-block;
    vertical-align: middle;
    text-align: center;
  }
  .brand__main {
    display: block;
    font-size: 84px;
    letter-spacing: 4px;
  }
  .brand__sub {
    display: block;
    font-size: 20px;
    letter-spacing: 3px;
    margin-top: 14px;
  }

  .person {
    position: absolute;
    left: 118px;
    top: 320px;
    width: 262px;
    text-align: right;
    font-family: "Questrial", sans-serif;
  }
  .person__name {
    font-size: 28px;
    color: var(--white);
    line-height: 1;
  }
  .person__first { color: var(--green); }
  .person__role {
    font-size: 15px;
    color: var(--light);
    margin-top: 6px;
  }
  .divider {
    position: absolute;
    left: 398px;
    top: 306px;
    width: 2px;
    height: 76px;
    background: var(--green);
  }
  .contact {
    position: absolute;
    left: 430px;
    top: 308px;
    list-style: none;
    font-family: "Questrial", sans-serif;
    font-size: 16px;
    color: var(--light);
  }
  .contact__item {
    display: flex;
    align-items: center;
    height: 22px;
  }
  .contact__icon {
    width: 12px;
    height: 12px;
    margin-right: 14px;
    fill: var(--green);
    flex: none;
  }

  .web {
    position: absolute;
    left: 0;
    right: 0;
    top: 384px;
    display: flex;
    align-items: center;
    justify-content: center;
    gap: 18px;
  }
  .web__rule {
    width: 160px;
    height: 3px;
    background: linear-gradient(90deg, rgba(255,255,255,0.1), var(--white));
    border-radius: 2px;
  }
  .web__rule--right {
    background: linear-gradient(90deg, var(--white), rgba(255,255,255,0.1));
  }
  .web__url {
    font-family: "Questrial", sans-serif;
    font-size: 18px;
    color: var(--white);
  }
  .web__accent { color: var(--green); }
</style>
</head>
<body>
<main class="canvas">

  <section class="card card--front" aria-label="Business card front">
    <div class="brand">
      <span class="brand__mark"></span><span class="brand__name">
        <span class="brand__main">TMW</span>
        <span class="brand__sub">HOME CRAFTING</span>
      </span>
    </div>

    <div class="person">
      <p class="person__name"><span class="person__first">Liam</span> Harcourt</p>
      <p class="person__role">General Manager</p>
    </div>

    <div class="divider"></div>

    <ul class="contact">
      <li class="contact__item">
        <svg class="contact__icon" viewBox="0 0 24 24" aria-hidden="true"><path d="M6.6 10.8a15.1 15.1 0 0 0 6.6 6.6l2.2-2.2c.3-.3.7-.4 1-.2 1.1.4 2.3.6 3.6.6.6 0 1 .4 1 1V20c0 .6-.4 1-1 1A17 17 0 0 1 3 4c0-.6.4-1 1-1h3.5c.6 0 1 .4 1 1 0 1.3.2 2.5.6 3.6.1.3 0 .7-.2 1z"/></svg>
        0400 555 018
      </li>
      <li class="contact__item">
        <svg class="contact__icon" viewBox="0 0 24 24" aria-hidden="true"><path d="M2 5h20v14H2z M2 5l10 7 10-7" /></svg>
        info@tmwhomecrafting.com.au
      </li>
      <li class="contact__item">
        <svg class="contact__icon" viewBox="0 0 24 24" aria-hidden="true"><path d="M12 2a7 7 0 0 0-7 7c0 5.2 7 13 7 13s7-7.8 7-13a7 7 0 0 0-7-7zm0 9.5a2.5 2.5 0 1 1 0-5 2.5 2.5 0 0 1 0 5z"/></svg>
        Riverbend, Tasmania, Australia
      </li>
    </ul>
  </section>

  <section class="card card--back" aria-label="Business card back">
    <div class="brand">
      <span class="brand__mark"></span><span class="brand__name">
        <span class="brand__main">TMW</span>
        <span class="brand__sub">HOME CRAFTING</span>
      </span>
    </div>

    <div class="web">
      <span class="web__rule"></span>
      <span class="web__url">www.<span class="web__accent">tmwhomecrafting</span>.com</span>
      <span class="web__rule web__rule--right"></span>
    </div>
  </section>

</main>
</body>
</html>
```